HearthMile business card and stationary design

We are looking for a simple yet elegant design for our mortgage company business card and stationary.

The card should include:
Name (Marcus Pell)
Title (CEO)
Phone Number (555-555-0182)
Address (48 Birchwell Court, Suite 314, Larkmere, NJ 00000)
Email (email@hearthmile.example)
"NMLS" i.e. (NMLS 61947)
"Company NMLS" (Company NMLS 274615)

Contact Information for Business Card

See above

```html
<!DOCTYPE html>
<html lang="en">
<head>
<meta charset="utf-8">
<title>HearthMile Business Card</title>
<link rel="stylesheet" href="https://fonts.googleapis.com/css2?family=Arimo:wght@400;700&family=Oswald:wght@500&display=swap">
<style>
  :root {
    --backdrop: #0b0b0c;
    --card: #171718;
    --accent: #00aeef;
    --ink: #ffffff;
    --ink-soft: #e6e6e6;
  }
  * { margin: 0; padding: 0; box-sizing: border-box; }
  html, body {
    width: 1200px; height: 900px; overflow: hidden;
    background: var(--backdrop);
    font-family: "Arimo", Arial, sans-serif;
    color: var(--ink);
  }
  .stage {
    width: 1200px; height: 900px;
    display: flex; flex-direction: column;
    align-items: center; justify-content: center;
    gap: 40px;
  }
  .card {
    position: relative;
    width: 660px; height: 377px;
    background: var(--card);
    overflow: hidden;
  }
  .card__band {
    position: absolute; left: 0; right: 0; bottom: 0;
    height: 10px; background: var(--accent);
  }

  /* Front */
  .card--front .brand {
    position: absolute; top: 130px; left: 0; right: 0;
    text-align: center;
    font-family: "Arimo", Arial, sans-serif;
    font-weight: 700; font-size: 70px; line-height: 1;
    letter-spacing: 1px; color: var(--ink);
  }
  .card--front .licences {
    position: absolute; top: 300px; left: 0; right: 0;
    text-align: center; font-size: 17px; letter-spacing: 0.5px;
  }
  .label { color: var(--accent); }
  .divider-slash { margin: 0 10px; }

  /* Back */
  .card--back .identity {
    position: absolute; top: 130px; left: 100px; width: 224px;
    text-align: right;
  }
  .identity__name {
    font-family: "Oswald", "Arial Narrow", sans-serif;
    font-weight: 500; font-size: 38px; line-height: 1;
    text-transform: uppercase; color: var(--accent);
    letter-spacing: -0.5px; white-space: nowrap;
  }
  .identity__title { font-size: 18px; margin-top: 4px; color: var(--ink-soft); }
  .card--back .rule {
    position: absolute; top: 140px; left: 344px;
    width: 1.5px; height: 82px; background: var(--accent);
  }
  .contact {
    position: absolute; top: 146px; left: 368px;
    list-style: none; font-size: 17px; line-height: 24px;
  }
  .contact li { display: flex; align-items: center; gap: 8px; white-space: nowrap; }
  .contact svg { width: 15px; height: 15px; flex: none; }
  .address {
    position: absolute; top: 298px; left: 0; right: 0;
    text-align: center; font-size: 18px; letter-spacing: 0.3px;
  }
</style>
</head>
<body>
<main class="stage">
  <section class="card card--front">
    <div class="brand">HearthMile</div>
    <p class="licences">
      <span class="label">NMLS</span> 61947<span class="divider-slash">|</span><span class="label">Company NMLS</span> 274615
    </p>
    <div class="card__band"></div>
  </section>

  <section class="card card--back">
    <div class="identity">
      <div class="identity__name">Marcus Pell</div>
      <div class="identity__title">CEO</div>
    </div>
    <div class="rule"></div>
    <ul class="contact">
      <li>
        <svg viewBox="0 0 24 24" fill="none" stroke="#00aeef" stroke-width="2.4" stroke-linecap="round" stroke-linejoin="round"><path d="M5 3h4l2 5-2.5 1.5a11 11 0 0 0 6 6L16 13l5 2v4a2 2 0 0 1-2 2A17 17 0 0 1 3 5a2 2 0 0 1 2-2z"/></svg>
        555-555-0182
      </li>
      <li>
        <svg viewBox="0 0 24 24" fill="none" stroke="#00aeef" stroke-width="2.4" stroke-linejoin="round"><rect x="2" y="5" width="20" height="14"/><path d="M2 5l10 8 10-8"/></svg>
        email@hearthmile.example
      </li>
      <li>
        <svg viewBox="0 0 24 24" fill="none" stroke="#00aeef" stroke-width="2"><circle cx="12" cy="12" r="10"/><ellipse cx="12" cy="12" rx="4" ry="10"/><path d="M2 12h20M4 7h16M4 17h16"/></svg>
        <span>www.<span class="label">hearthmile</span>.example</span>
      </li>
    </ul>
    <p class="address">48 Birchwell Court, Suite 314, Larkmere, NJ 00000</p>
    <div class="card__band"></div>
  </section>
</main>
</body>
</html>
```